TALMORK

The business want a professional looking business card. We have a scetch we will add but want the extra upgrade, and would like more suggestions for variations of our business cards.

```html
<!DOCTYPE html>
<html lang="en">
<head>
<meta charset="utf-8">
<title>TALMORK — Business Card</title>
<link href="https://fonts.googleapis.com/css2?family=Philosopher:wght@400;700&family=Nunito:wght@400;500&display=swap" rel="stylesheet">
<style>
  :root {
    --backdrop: #e4e4e6;
    --card-light: #f7f3e3;
    --card-dark: #efe8d0;
    --ink-brown: #5a3a16;
    --ink-soft: #6b4a22;
    --gold: #b48a3a;
    --gold-light: #d2b169;
  }
  * { margin: 0; padding: 0; box-sizing: border-box; }
  html, body { width: 1200px; height: 805px; overflow: hidden; }
  body {
    background: var(--backdrop);
    position: relative;
    font-family: "Nunito", sans-serif;
  }
  .card {
    position: absolute;
    top: 232px;
    width: 510px;
    height: 341px;
    background: linear-gradient(135deg, var(--card-dark) 0%, var(--card-light) 60%, var(--card-light) 100%);
  }
  .card--front { left: 66px; }
  .card--back { left: 624px; }

  .holder-name {
    position: absolute; left: 47px; top: 46px;
    font-family: "Philosopher", sans-serif; font-weight: 700;
    font-size: 32px; color: var(--ink-brown); letter-spacing: 0.2px;
  }
  .holder-role {
    position: absolute; left: 47px; top: 100px;
    font-size: 22px; color: var(--ink-brown);
  }
  .holder-sub {
    position: absolute; left: 47px; top: 131px;
    font-size: 16px; color: var(--ink-soft);
  }
  .contact-list { position: absolute; left: 47px; top: 210px; list-style: none; }
  .contact-item {
    display: flex; align-items: center; height: 32px;
    font-size: 19px; color: var(--ink-brown);
  }
  .contact-icon { width: 20px; height: 20px; margin-right: 13px; flex: none; }

  .brand-lockup {
    position: absolute; display: flex; flex-direction: column; align-items: center;
    color: var(--gold);
  }
  .brand-lockup--small { left: 372px; top: 212px; width: 120px; }
  .brand-lockup--large { left: 0; top: 78px; width: 100%; }
  .brand-dot { border-radius: 50%; background: var(--gold); }
  .brand-lockup--small .brand-dot { width: 26px; height: 26px; margin-bottom: 12px; }
  .brand-lockup--large .brand-dot { width: 58px; height: 58px; margin-bottom: 26px; }
  .brand-name { font-family: "Philosopher", sans-serif; font-weight: 400; color: var(--gold); }
  .brand-lockup--small .brand-name { font-size: 21px; letter-spacing: 2px; }
  .brand-lockup--large .brand-name { font-size: 44px; letter-spacing: 6px; }
  .brand-since { color: var(--gold); font-weight: 500; }
  .brand-lockup--small .brand-since { font-size: 6px; letter-spacing: 1.5px; margin-top: 2px; }
  .brand-lockup--large .brand-since { font-size: 14px; letter-spacing: 3.5px; margin-top: 8px; color: var(--ink-soft); }
</style>
</head>
<body>
  <section class="card card--front">
    <h1 class="holder-name">Henrik Olav Brennmoen</h1>
    <p class="holder-role">CEO &amp; Founder</p>
    <p class="holder-sub">Henrik Olav Brennmoen</p>
    <ul class="contact-list">
      <li class="contact-item">
        <svg class="contact-icon" viewBox="0 0 20 20" aria-hidden="true"><rect x="5" y="1.5" width="10" height="17" rx="2" fill="none" stroke="#5a3a16" stroke-width="1.6"/><line x1="8.5" y1="15.5" x2="11.5" y2="15.5" stroke="#5a3a16" stroke-width="1.6"/></svg>
        004791234567
      </li>
      <li class="contact-item">
        <svg class="contact-icon" viewBox="0 0 20 20" aria-hidden="true"><rect x="1.5" y="4.5" width="17" height="11" fill="#5a3a16"/><polyline points="1.5,4.5 10,11 18.5,4.5" fill="none" stroke="#f4efdc" stroke-width="1.3"/></svg>
        talmork.llc@postmail.com
      </li>
      <li class="contact-item">
        <svg class="contact-icon" viewBox="0 0 20 20" aria-hidden="true"><circle cx="10" cy="10" r="8" fill="none" stroke="#5a3a16" stroke-width="1.6"/><ellipse cx="10" cy="10" rx="3.5" ry="8" fill="none" stroke="#5a3a16" stroke-width="1.2"/><line x1="2" y1="10" x2="18" y2="10" stroke="#5a3a16" stroke-width="1.2"/></svg>
        www.talmork.llc
      </li>
    </ul>
    <div class="brand-lockup brand-lockup--small">
      <span class="brand-dot"></span>
      <span class="brand-name">TALMORK</span>
      <span class="brand-since">SINCE 2026</span>
    </div>
  </section>

  <section class="card card--back">
    <div class="brand-lockup brand-lockup--large">
      <span class="brand-dot"></span>
      <span class="brand-name">TALMORK</span>
      <span class="brand-since">SINCE 2026</span>
    </div>
  </section>
</body>
</html>
```